Business card for law firm

Need business card for new law firm. Think confident, authoritative, conservative, but not stuffy or old-fashioned.

Contact Information for Business Card

Content for card - logo (uploaded), plus the following:

Paul Whitcombe (larger font)
Managing Partner (larger font, but not as large as name)
Level 9, 7 Ferris Lane
Sydney NSW 2000
Main Tel 02 9364 2710
Direct Tel 02 8472 3159
Email paul@qvlegal.com.au
www.qvlegal.com.au

Letterhead design should include logo plus:
Level 9, 7 Ferris Lane
Sydney NSW 2000
Tel 02 8472 3159
www.qvlegal.com.au

```html
<!DOCTYPE html>
<html lang="en">
<head>
<meta charset="utf-8">
<title>Quayview Legal – Business Card</title>
<link rel="stylesheet" href="https://fonts.googleapis.com/css2?family=Open+Sans:wght@400;600;700&display=swap">
<style>
  :root {
    --navy: #001b54;
    --black: #050505;
    --white: #ffffff;
    --ink: #111111;
    --edge: #a9abae;
    --bg-light: #ececed;
    --bg-dark: #c9cacc;
  }
  * { box-sizing: border-box; margin: 0; padding: 0; }
  html, body { width: 1200px; height: 1142px; overflow: hidden; }
  body {
    background: linear-gradient(135deg, var(--bg-light) 0%, var(--bg-dark) 100%);
    font-family: "Open Sans", Arial, sans-serif;
    position: relative;
  }
  .card {
    position: absolute;
    width: 765px;
    height: 437px;
    border-radius: 40px;
    border: 1px solid var(--edge);
    background: var(--white);
    overflow: hidden;
  }
  .card--front { left: 94px; top: 113px; }
  .card--back { left: 335px; top: 603px; }

  /* brand block */
  .brand { position: absolute; left: 0; right: 0; text-align: center; color: var(--ink); font-weight: 400; }
  .brand__mark { display: block; margin: 0 auto; background: var(--navy); }
  .brand__name { display: block; letter-spacing: 2px; line-height: 1; }
  .brand__tag { display: block; line-height: 1; }

  .card--front .brand { top: 24px; }
  .card--front .brand__mark { width: 58px; height: 58px; margin-bottom: 18px; }
  .card--front .brand__name { font-size: 38px; }
  .card--front .brand__tag { font-size: 14px; letter-spacing: 20px; margin-top: 8px; padding-left: 20px; }

  .card--back .brand { top: 60px; }
  .card--back .brand__mark { width: 90px; height: 90px; margin-bottom: 40px; }
  .card--back .brand__name { font-size: 50px; }
  .card--back .brand__tag { font-size: 20px; letter-spacing: 28px; margin-top: 16px; padding-left: 28px; }

  /* front bands */
  .band-top { position: absolute; left: 0; top: 223px; width: 100%; height: 45px; background: var(--black); }
  .band-name { position: absolute; left: 0; top: 223px; width: 430px; height: 92px; background: var(--black); }
  .band-rule { position: absolute; left: 0; top: 315px; width: 430px; height: 2px; background: var(--white); }
  .panel-navy { position: absolute; left: 0; top: 317px; width: 100%; height: 120px; background: var(--navy); }
  .panel-navy-right { position: absolute; left: 430px; top: 268px; right: 0; height: 60px; background: var(--navy); }

  .portrait {
    position: absolute; left: 338px; top: 213px; width: 106px; height: 106px;
    border-radius: 50%; background: var(--navy); border: 3px solid var(--white);
    box-shadow: 0 0 0 2px var(--navy);
  }

  .person { position: absolute; left: 53px; top: 240px; color: var(--white); text-align: center; width: 240px; }
  .person__name { font-weight: 700; font-size: 27px; line-height: 1.1; white-space: nowrap; }
  .person__role { font-size: 20px; line-height: 1.4; }

  .address { position: absolute; left: 47px; top: 345px; color: var(--white); font-size: 21px; line-height: 31px; }

  .contacts { position: absolute; left: 456px; top: 286px; list-style: none; color: var(--white); font-size: 21px; line-height: 34.5px; }
  .contacts li { display: flex; align-items: center; white-space: nowrap; }
  .contacts svg { width: 18px; height: 18px; margin-right: 7px; flex: none; }

  .web { position: absolute; left: 0; right: 0; top: 368px; text-align: center; font-size: 25px; letter-spacing: 4px; color: var(--ink); }
  .web strong { color: var(--navy); font-weight: 700; }
</style>
</head>
<body>

<section class="card card--front" aria-label="Business card front">
  <div class="brand">
    <span class="brand__mark"></span>
    <span class="brand__name">QUAYVIEW</span>
    <span class="brand__tag">LEGAL</span>
  </div>

  <div class="band-top"></div>
  <div class="band-name"></div>
  <div class="panel-navy-right"></div>
  <div class="band-rule"></div>
  <div class="panel-navy"></div>
  <div class="portrait" role="img" aria-label="Profile photo of Paul Whitcombe"></div>

  <div class="person">
    <p class="person__name">PAUL WHITCOMBE</p>
    <p class="person__role">MANAGING PARTNER</p>
  </div>

  <address class="address" style="font-style:normal">
    Level 9, 7 Ferris Lane<br>Sydney NSW 2000
  </address>

  <ul class="contacts">
    <li><svg viewBox="0 0 20 20" fill="none" stroke="currentColor" stroke-width="2"><circle cx="10" cy="10" r="8"/><path d="M7 6c-1 3 2 8 6 8" stroke-linecap="round"/></svg>02 9364 2710(Main)</li>
    <li><svg viewBox="0 0 20 20" fill="none" stroke="currentColor" stroke-width="2"><circle cx="10" cy="10" r="8"/><path d="M7 6c-1 3 2 8 6 8" stroke-linecap="round"/></svg>02 8472 3159(Direct)</li>
    <li><svg viewBox="0 0 20 20" fill="currentColor"><path d="M2 8l8-5 8 5v9H2z"/><path d="M3 9l7 5 7-5" fill="none" stroke="#001b54" stroke-width="1.5"/></svg>paul@qvlegal.com.au</li>
    <li><svg viewBox="0 0 20 20" fill="none" stroke="currentColor" stroke-width="1.5"><circle cx="10" cy="10" r="8"/><ellipse cx="10" cy="10" rx="3.5" ry="8"/><path d="M2 10h16M3.5 6h13M3.5 14h13"/></svg>www.qvlegal.com.au</li>
  </ul>
</section>

<section class="card card--back" aria-label="Business card back">
  <div class="brand">
    <span class="brand__mark"></span>
    <span class="brand__name">QUAYVIEW</span>
    <span class="brand__tag">LEGAL</span>
  </div>
  <p class="web">www.<strong>qvlegal</strong>.com.au</p>
</section>

</body>
</html>
```